Website Design for a different kind of Business Consulting organisation needed!

We need a website design that reflects who we are, the simplicity of our consulting business and with a focus on our priority - to help our clients deliver, or execute - the "e" in Vantor-i.

Our key high level requirements are:
1) Simple and intuitive look and feel
2) Integration with all key social media platforms, twitter, facebook, linkedin, tumblr.

10 pages, tops.
- Main page - Welcome
- About Us/ Who are Vantor-i?
- 5 services pages - Project Management, Business Process Management, Change Management, Business Analysis and Finance Systems
- Contact Us

Something like:
http://www.lumvexhold.example/

Vantor-i is a registered trademark and all Logos and other branded material are attached for reference.

So, what’s our gig: A few snippets from previous work...

We are a different kind of business consulting group. We partner with our clients to help them deliver change. We don't just provide them with the theory. We also provide them with the leadership and capability to execute the change.

We aren’t a one stop shop, and we don’t offer cookie cutter solutions. We’re a boutique consulting firm covering Project Management, Business Process Management, Change Management and Business Analytics.

Vantor-i is a professional services organisation that partners with their clients to lead the execution of strategic process and system improvement initiatives. Vantor-i combines hands on delivery with coaching in best practice methodologies and approaches to build their clients capabilities to ensure their ongoing success in project implementations.

UPDATES:

Thanks to everyone who has submitted designs so far. The standard of designs coming through is quite high, with lots of professional designs that nail the design brief. Eliminating them is proving to be quite challenging.

A few updates to the job brief:
- Please make sure the design fits on one page. We would like all of our information to be on the first page that people see without them having to scroll down
- Please ensure you include the FIVE services we offer in the design
- Please use corporate images/istock photos in your designs which are relevant to our business
- Please add a section for a live twitter feed from our twitter account and a link to google+
- Please add a section for news/updates

Also, if you are able to build a site once a design is selected, please let us know.

Thanks,

Maribel.

Target Market(s)

Our target customers are large enterprises in Australia that are growing rapidly and have recently (last 24 months) undertaken or are currently undergoing software implementations and business process improvement programs. These businesses have a turnover of $100m or above and are working hard to differentiate themselves from their competitors but are not seeing the return on investment promised by software vendors and process improvement initiatives.

Industry/Entity Type

Leadership

Requirements
Must have
• Collaboration / Training / Workshop / Consulting images all of a professional nature.
Simple, non-cluttered look with plenty of white space.

```html
<!DOCTYPE html>
<html lang="en">
<head>
<meta charset="utf-8">
<title>Vantor-i – Change Management</title>
<link href="https://fonts.googleapis.com/css2?family=Open+Sans:wght@400;600;700&display=swap" rel="stylesheet">
<style>
:root{
  --brand:#0b51a4;
  --brand-light:#4f8fd2;
  --text:#555;
  --muted:#9a9a9a;
  --rule:#dcdcdc;
  --social:#7a7a7a;
  --white:#fff;
}
*{box-sizing:border-box;margin:0;padding:0}
html,body{width:976px;height:1200px;overflow:hidden;background:var(--white)}
body{font-family:"Open Sans",sans-serif;color:var(--text)}
.page{width:1200px;height:1476px;position:relative;transform:scale(0.81333);transform-origin:0 0}
.top-bar{position:absolute;left:0;top:0;width:1200px;height:6px;background:var(--brand)}

.logo{position:absolute;left:120px;top:22px;color:var(--brand);font-weight:600;font-size:54px;line-height:60px;letter-spacing:1px}
.logo small{position:absolute;left:142px;top:52px;font-size:10px;line-height:12px;letter-spacing:0;font-weight:400}

.social-top{position:absolute;left:922px;top:17px;display:flex;gap:9px}
.social-top span{width:33px;height:33px;border-radius:50%;background:var(--social)}
.social-top span.active{background:var(--brand)}

.main-nav{position:absolute;top:72px;left:0;font-size:15px;font-weight:600;text-transform:uppercase;color:var(--muted)}
.main-nav a{position:absolute;top:0;line-height:21px;color:inherit;text-decoration:none;white-space:nowrap}
.main-nav a.current{background:var(--brand);color:var(--white);width:106px;text-align:center;font-size:15px}

.dropdown{position:absolute;left:739px;top:93px;width:232px;height:157px;background:var(--brand);padding-top:2px;z-index:5}
.dropdown li{list-style:none;height:30px;display:flex;align-items:center;color:var(--white);font-size:12.5px}
.dropdown li.active{background:var(--brand-light)}
.dropdown svg{width:22px;height:22px;margin:0 13px 0 14px}

.rule{position:absolute;left:120px;width:960px;height:1px;background:var(--rule)}

.intro-icon{position:absolute;left:120px;top:152px;width:101px;height:101px}
.intro{position:absolute;left:252px;top:148px;width:828px}
h1,h2{color:var(--brand);font-weight:600}
.intro h1{font-size:27px;line-height:36px;margin-bottom:6px}
p{font-size:16px;line-height:25px}
.intro p+p{margin-top:8px}

.photo{border:0}
.photo-meeting{position:absolute;left:120px;top:425px;width:397px;height:342px;background:linear-gradient(120deg,#c9d3dc,#eef2f5 45%,#8fa3b8 80%,#6d7f94)}
.feature{position:absolute;left:572px;top:417px;width:508px}
.feature h2{font-size:25px;line-height:36px;margin-bottom:1px}
.feature h3{font-size:18px;font-weight:600;color:#444;margin:24px 0 4px;line-height:26px}
.ticks{list-style:none}
.ticks li{font-size:16px;line-height:30px;padding-left:36px;position:relative}
.ticks svg{position:absolute;left:4px;top:6px;width:20px;height:18px}
.feature .closing{margin-top:22px;padding-left:4px}

.article{position:absolute;left:130px;top:831px;width:955px}
.article h2{font-size:25px;line-height:36px;margin-bottom:1px;width:520px}
.photo-dinner{float:right;width:397px;height:341px;margin:8px 6px 24px 42px;background:linear-gradient(135deg,#4a3226,#7a5a44 40%,#bfbab4 70%,#3a2a22)}
.article p+p{margin-top:25px}
.article p{width:auto}

.site-footer{position:absolute;left:0;top:1360px;width:1200px;height:116px;background:var(--brand);color:var(--white);font-size:12.5px}
.site-footer h4{font-size:13.5px;font-weight:700;line-height:18px;margin-bottom:2px}
.site-footer .col{position:absolute;top:19px;line-height:19px}
.site-footer a{color:inherit;text-decoration:none}
.footer-social{display:flex;gap:8px;margin-top:7px}
.footer-social span{width:32px;height:32px;border-radius:50%;background:var(--white)}
.page-links{display:grid;grid-template-columns:74px auto}
.footer-logo{position:absolute;left:868px;top:14px;font-size:44px;line-height:50px;font-weight:600;letter-spacing:1px}
.footer-logo small{position:absolute;left:118px;top:43px;font-size:9px;line-height:10px;letter-spacing:0;font-weight:400}
.copyright{position:absolute;left:869px;top:73px}
</style>
</head>
<body>
<div class="page">
  <div class="top-bar"></div>

  <header>
    <div class="logo">Vantor-i<small>Pty Ltd</small></div>
    <div class="social-top" aria-label="Social links">
      <span></span><span></span><span></span><span class="active"></span>
    </div>
    <nav class="main-nav">
      <a style="left:576px">Home</a>
      <a style="left:665px">About</a>
      <a class="current" style="left:739px">Services</a>
      <a style="left:867px">Partners</a>
      <a style="left:983px">Contact</a>
    </nav>
    <ul class="dropdown">
      <li><svg viewBox="0 0 22 22" fill="#fff"><rect x="9" y="2" width="4" height="4"/><rect x="10.5" y="6" width="1" height="4"/><rect x="3" y="10" width="16" height="1"/><rect x="2" y="14" width="4" height="5"/><rect x="9" y="14" width="4" height="5"/><rect x="16" y="14" width="4" height="5"/></svg>Project Management</li>
      <li><svg viewBox="0 0 22 22" fill="#fff"><rect x="2" y="2" width="4" height="16"/><rect x="8" y="4" width="12" height="2"/><rect x="8" y="9" width="9" height="2"/><rect x="8" y="14" width="12" height="2"/><rect x="2" y="19" width="18" height="1"/></svg>Business Process Management</li>
      <li class="active"><svg viewBox="0 0 22 22" fill="none" stroke="#fff" stroke-width="2"><path d="M6 9a6 6 0 0 1 10-3"/><path d="M16 13a6 6 0 0 1-10 3"/><rect x="3" y="3" width="4" height="4" fill="#fff" stroke="none"/><rect x="15" y="15" width="4" height="4" fill="#fff" stroke="none"/></svg>Change Management</li>
      <li><svg viewBox="0 0 22 22" fill="#fff"><rect x="2" y="12" width="4" height="7"/><rect x="8" y="8" width="4" height="11"/><rect x="14" y="4" width="4" height="15"/></svg>Business Analysis</li>
      <li><svg viewBox="0 0 22 22" fill="none" stroke="#fff" stroke-width="2"><circle cx="11" cy="11" r="5"/><circle cx="11" cy="11" r="1.5" fill="#fff"/><path d="M11 2v3M11 17v3M2 11h3M17 11h3"/></svg>Finance System</li>
    </ul>
  </header>

  <div class="rule" style="top:116px"></div>

  <section>
    <svg class="intro-icon" viewBox="0 0 101 101" aria-hidden="true">
      <circle cx="50.5" cy="50.5" r="50.5" fill="var(--brand)"/>
      <g fill="#fff">
        <circle cx="35" cy="33" r="5"/><rect x="27" y="40" width="16" height="10" rx="3"/>
        <circle cx="66" cy="56" r="5"/><rect x="58" y="63" width="16" height="10" rx="3"/>
      </g>
      <g fill="none" stroke="#fff" stroke-width="3">
        <path d="M50 28a16 16 0 0 1 17 14"/><path d="M51 74a16 16 0 0 1-18-13"/>
      </g>
      <path d="M62 40l5 6 4-7z M38 64l-5-6-4 7z" fill="#fff"/>
    </svg>
    <div class="intro">
      <h1>Change Management</h1>
      <p>Sed ut perspiciatis unde omnis iste natus error sit voluptatem accusantium doloremque laudantium, totam rem aperiam, eaque ipsa quae ab illo inventore veritatis et quasi architecto beatae vitae dicta sunt explicabo. Nemo enim ipsam voluptatem quia voluptas sit aspernatur aut odit aut fug set med itom.</p>
      <p>Lorem ipsum dolor sit amet, consectetur adipisicing elit, sed do eiusmod tempor incididunt ut labore et dolore in voluptate velit esse cillum dolore eu fugiat nulla pariatur.</p>
    </div>
  </section>

  <div class="rule" style="top:369px"></div>

  <section>
    <div class="photo photo-meeting" role="img" aria-label="Photo of two businessmen in a meeting, one looking at a phone"></div>
    <div class="feature">
      <h2>Lorem Ipsum Text Header h4 25px/33px</h2>
      <p>Sed ut perspiciatis unde omnis iste natus error sit voluptatem asantium doloremque laudantium, totam rem aperiam, eaque ipsa quae cabo. Nemo enim ipsam voluptatem quia voluptas.</p>
      <h3>Sample List Option</h3>
      <ul class="ticks">
        <li><svg viewBox="0 0 20 18"><path d="M1 10l6 6L19 2" fill="none" stroke="var(--brand)" stroke-width="4"/></svg>Sed ut perspiciatis unde omnis iste natus error</li>
        <li><svg viewBox="0 0 20 18"><path d="M1 10l6 6L19 2" fill="none" stroke="var(--brand)" stroke-width="4"/></svg>Sit voluptatem accusantium doloremque laudantium</li>
        <li><svg viewBox="0 0 20 18"><path d="M1 10l6 6L19 2" fill="none" stroke="var(--brand)" stroke-width="4"/></svg>veritatis et quasi architecto beatae vitae dicta sunt</li>
      </ul>
      <p class="closing">Nemo enim ipsam voluptatem quia voluptas sit asper atur aut odit aut fugit, sed quia consequuntur magni dolores eos qui ratione voluptatem sequi nesciunt. Neque porro quisquam est.</p>
    </div>
  </section>

  <section class="article">
    <h2>This is h4 25px with 33px Leading</h2>
    <div class="photo photo-dinner" role="img" aria-label="Photo of two senior businessmen talking over dinner in a wine cellar"></div>
    <p>Sed ut perspiciatis unde omnis iste natus error sit voluptatem accusantium doloremque laudantium, totam rem aperiam, eaque ipsa quae ab illo inventore veritatis et quasi architecto beatae vitae dicta sunt explicabo. <strong>This is bold Nemo enim ipsam</strong> volupteius modi tempora incidunt ut labore et dolore magnam aliquam quaerat voluptatem. Ut enim ad minima veniam, quis nostrum exercitationem ullam corporis suscipit laboriosam?</p>
    <p>Nisi ut aliquid ex ea commodi consequatur qui dolorem ipsum quia dolor sit amet, consectetur, adipisci velit, sed quia non numquam eius modi tempora incidunt ut labore et dolore magnam aliquam quaerat voluptatem. Ut enim ad minima veniam, quis nostrum exercitationem ullam corporis suscipit laboriosam, nisi ut aliquid ex ea ut perspiciatis unde omnis iste natus error sit voluptatem accusantium doloremque laudantium, totam rem aperiam, eaque ipsa quae ab illo inventore veritatis et quasi architecto beatae vitae dicta sunt explicabo. <strong>This is bold Nemo enim ipsam</strong> volupteius modi tempora incidunt ut labore et dolore magnam aliquam quaerat voluptatem. Ut enim ad minima veniam, quis nostrum exercitationem ullam corporis suscipit laboriosam, nisi ut aliquid ex ea commodi consequatur?</p>
  </section>

  <footer class="site-footer">
    <div class="col" style="left:121px">
      <h4>CONNECT WITH US</h4>
      <div>on social media network</div>
      <div class="footer-social"><span></span><span></span><span></span><span></span></div>
    </div>
    <div class="col" style="left:331px">
      <h4>PAGES</h4>
      <div class="page-links">
        <a>Home</a><a>Term &amp; Conditions</a>
        <a>About</a><a>FAQ</a>
        <a>Services</a><a>Partners</a>
      </div>
    </div>
    <div class="col" style="left:569px">
      <h4>CONTACT DETAILS</h4>
      <div>p: +61 3 555 010 224&nbsp; f: +61 3 555 019 871</div>
      <div>Level 4, 12 Harbour Lane, Melbourne,</div>
      <div>Australia, 3000</div>
    </div>
    <div class="footer-logo">Vantor-i<small>Pty Ltd</small></div>
    <div class="copyright">Copyright © 2014 All Rights Reserved</div>
  </footer>
</div>
</body>
</html>
```